High-end construction company needs a business card design

We need a modern looking business card that draws people in, is memorable and looks so good people will want to sick it on their fridges.
On the first side what is needed are:
Logo
My name - Tomasz Brelwik
Title - Managing Director
Website - www.varkelt.co.uk
Email - tomasz@varkelt.co.uk
Telephone - 020 5194 6281
Mobile - 07845139072
On the back side was is needed is a list of all the services we provide:
-Kitchen Renovations
-Bathroom Renovations
-House Renovations
-Garage Conversions
-Extensions
-Loft Conversions
-Conservatories
-Carpentry
-Tiling
-Electrical
-Plumbing & Heating
-Bricklaying
-Landscaping
-Decorating
-Plastering
We would like the colours to be the same shades as on the logo with grey or black for the words.
Target Market(s)
Anyone who needs building work done
Contact Information for Business Card
This business card is for a construction company which strives to deliver excellent service and quality.
The look and feel of the card should represent this.
Requirements
Must have
- On the first side what is needed are:
Logo
My name - Tomasz Brelwik
Title - Managing Director
Website - www.varkelt.co.uk
Email - tomasz@varkelt.co.uk
Telephone - 020 5194 6281
Mobile - 07845139072
Nice to have
- Cool looking features

```html
<!DOCTYPE html>
<html lang="en">
<head>
<meta charset="utf-8">
<title>Varkelt Construction Ltd – Business Card</title>
<link rel="stylesheet" href="https://fonts.googleapis.com/css2?family=Archivo+Black&family=Arimo:wght@400;700&display=swap">
<style>
  :root {
    --bg: #1f1f1f;
    --green-light: #76bf43;
    --green-dark: #4a8f3c;
    --white: #ffffff;
    --ink: #2b2b2b;
    --rule: #c9c9c9;
  }
  * { box-sizing: border-box; margin: 0; padding: 0; }
  html, body { width: 1200px; height: 1015px; overflow: hidden; background: var(--bg); }
  body { font-family: "Arimo", Arial, sans-serif; position: relative; }

  .card {
    position: absolute;
    left: 180px;
    width: 840px;
    height: 480px;
    overflow: hidden;
  }

  /* ---------- Services side ---------- */
  .card--services { top: 20px; background: var(--green-light); }
  .card--services .services-band {
    position: absolute; left: 0; right: 0; top: 270px; bottom: 0;
    background: var(--green-dark);
  }
  .brand {
    position: absolute;
    display: flex; align-items: center; gap: 12px;
    font-family: "Arimo", Arial, sans-serif;
    font-weight: 700;
    letter-spacing: 1px;
    white-space: nowrap;
  }
  .brand__mark { flex: none; }
  .card--services .brand {
    left: 0; right: 0; top: 108px; justify-content: center;
    color: var(--white); font-size: 40px;
  }
  .card--services .brand__mark { width: 22px; height: 22px; background: var(--white); }

  .services {
    position: absolute; left: 40px; right: 30px; top: 300px;
    display: flex; justify-content: space-between;
  }
  .services__col { list-style: none; }
  .services__item {
    color: var(--white); font-size: 23px; line-height: 32px;
    padding-left: 20px; position: relative; white-space: nowrap;
  }
  .services__item::before {
    content: ""; position: absolute; left: 0; top: 12px;
    width: 9px; height: 9px; border-radius: 50%; background: var(--white);
  }

  /* ---------- Contact side ---------- */
  .card--contact { top: 515px; background: var(--white); }
  .card--contact .brand {
    left: 40px; top: 222px; color: var(--green-light); font-size: 22px;
  }
  .card--contact .brand__mark { width: 16px; height: 16px; background: var(--green-light); }
  .divider {
    position: absolute; left: 470px; top: 70px; width: 1px; height: 250px;
    background: var(--rule);
  }
  .person { position: absolute; left: 500px; top: 78px; }
  .person__name {
    font-family: "Archivo Black", Arial, sans-serif;
    color: var(--green-light); font-size: 27px; line-height: 32px;
    text-transform: uppercase; white-space: nowrap;
  }
  .person__title { color: var(--ink); font-size: 21px; margin-top: 4px; }
  .contacts { list-style: none; margin-top: 30px; }
  .contacts__item {
    display: flex; align-items: center; gap: 12px;
    color: var(--ink); font-size: 20px; line-height: 31px; white-space: nowrap;
  }
  .contacts__item--web { color: var(--green-dark); }
  .contacts__icon { width: 20px; height: 20px; flex: none; fill: var(--green-light); }

  .stripe-light {
    position: absolute; left: 0; right: 0; bottom: 0; height: 40px;
    background: var(--green-light);
  }
  .stripe-dark {
    position: absolute; left: 520px; right: 0; bottom: 0; height: 70px;
    background: var(--green-dark);
    border-left: 8px solid var(--white);
  }
</style>
</head>
<body>

<section class="card card--services" aria-label="Services side">
  <div class="services-band"></div>
  <div class="brand"><span class="brand__mark"></span>VARKELT CONSTRUCTION LTD</div>
  <div class="services">
    <ul class="services__col">
      <li class="services__item">Kitchen Renovations</li>
      <li class="services__item">Bathroom Renovations</li>
      <li class="services__item">House Renovations</li>
      <li class="services__item">Garage Conversions</li>
      <li class="services__item">Extensions</li>
    </ul>
    <ul class="services__col">
      <li class="services__item">Loft Conversions</li>
      <li class="services__item">Conservatories</li>
      <li class="services__item">Carpentry</li>
      <li class="services__item">Tiling</li>
      <li class="services__item">Electrical</li>
    </ul>
    <ul class="services__col">
      <li class="services__item">Plumbing &amp; Heating</li>
      <li class="services__item">Bricklaying</li>
      <li class="services__item">Landscaping</li>
      <li class="services__item">Decorating</li>
      <li class="services__item">Plastering</li>
    </ul>
  </div>
</section>

<section class="card card--contact" aria-label="Contact side">
  <div class="brand"><span class="brand__mark"></span>VARKELT CONSTRUCTION LTD</div>
  <div class="divider"></div>
  <div class="person">
    <h1 class="person__name">Tomasz Brelwik</h1>
    <p class="person__title">Managing Director</p>
    <ul class="contacts">
      <li class="contacts__item">
        <svg class="contacts__icon" viewBox="0 0 20 20" aria-hidden="true"><path d="M4 2l4 4-2 2c1 2.5 3.5 5 6 6l2-2 4 4-3 3C8 18 2 12 1 5z"/></svg>
        020 5194 6281
      </li>
      <li class="contacts__item">
        <svg class="contacts__icon" viewBox="0 0 20 20" aria-hidden="true"><path d="M5 1h10v18H5zM7 3v12h6V3zM9 16h2v2H9z" fill-rule="evenodd"/></svg>
        07845139072
      </li>
      <li class="contacts__item">
        <svg class="contacts__icon" viewBox="0 0 20 20" aria-hidden="true"><path d="M1 4h18v12H1z"/><path d="M2 5l8 6 8-6" stroke="#fff" stroke-width="1.4" fill="none"/></svg>
        tomasz@varkelt.co.uk
      </li>
      <li class="contacts__item contacts__item--web">
        <svg class="contacts__icon" viewBox="0 0 20 20" aria-hidden="true"><circle cx="10" cy="10" r="9"/><path d="M1 10h18M10 1v18M4 4.5c3.5 2 8.5 2 12 0M4 15.5c3.5-2 8.5-2 12 0" stroke="#fff" stroke-width="1.2" fill="none"/><ellipse cx="10" cy="10" rx="4" ry="9" stroke="#fff" stroke-width="1.2" fill="none"/></svg>
        www.varkelt.co.uk
      </li>
    </ul>
  </div>
  <div class="stripe-light"></div>
  <div class="stripe-dark"></div>
</section>

</body>
</html>
```